Coastal Learner Bureau business cards

Australian company about to start offering its services. We recruit international students to come to study English, vocational education and postgraduate courses in Australia. We help them find the institution and select the right city they want to come to Australia. We are a young, online oriented and supportive agency. Our clients are between 18 and 35 years old, mainly University students, young professionals or people with work experience. We provide much more information that any other agency offer. We administrate a Facebook group with more than 11.000 members that daily ask questions about general information when coming to Australia, while they are here and even after they leave the country

Target Market(s)

International students from South America, Central America and Europe

Industry/Entity Type

Student

Contact Information for Business Card

Tomas Bilbrea
Managing Director
tomas@kelvarin.com.au
www.kelvoria.com.au
+61 491058264
Portvale, Australia

Font styles to use
Serif
Sans Serif

Colors

Designer to choose colors to be used in the design.

Requirements
Must have
• Horizontal design
• Standard business card size and shape. If font uses green or yellow colours, they will have to match the ones from the logo
Nice to have
• UPDATE: Use the contents of the green image to design one of the card sides. Use our logo in the background of that side as watermark.
• Passport image, or immigration stamps. A picture of the Yarra River (from Melbourne) would be cool as well.
Should not have
• Non-standard business card size and shape
• Not black as the background colour of any sides as we are not a VIP agency or a hight class service. We are orientes to young people and they like colours, pictures, something attractive.
• Vertical design
• NO YELLOW or BLACK AS THE BACKGROUND COLOUR OF ANY SIDE OF THE BIZ CARD

```html
<!DOCTYPE html>
<html lang="en">
<head>
<meta charset="utf-8">
<title>Kelvoria business cards</title>
<link href="https://fonts.googleapis.com/css2?family=Roboto:wght@400;500;700&family=Roboto+Condensed:wght@500;700&display=swap" rel="stylesheet">
<style>
  :root {
    --bg: #2a2a2a;
    --paper: #f2f2f2;
    --green: #0f5c3c;
    --yellow: #e0b512;
    --ink: #444444;
    --white: #ffffff;
  }
  * { box-sizing: border-box; margin: 0; padding: 0; }
  html, body {
    width: 1200px; height: 960px; overflow: hidden;
    background: var(--bg);
    font-family: "Roboto", Arial, sans-serif;
  }
  .canvas { position: relative; width: 1200px; height: 960px; }

  .card {
    position: absolute;
    width: 600px; height: 343px;
    overflow: hidden;
  }
  .card--front { left: 314px; top: 113px; background: var(--paper); }
  .card--back  { left: 311px; top: 472px; background: var(--green); }

  .front__accent {
    position: absolute; left: 0; top: 56px;
    width: 13px; height: 39px; background: var(--green);
  }
  .front__name {
    position: absolute; left: 44px; top: 53px;
    font-family: "Roboto Condensed", Arial, sans-serif;
    font-weight: 700; font-size: 23px; line-height: 26px; color: var(--green);
    letter-spacing: 0.2px;
  }
  .front__title {
    position: absolute; left: 44px; top: 79px;
    font-family: "Roboto", Arial, sans-serif;
    font-weight: 500; font-size: 15px; line-height: 18px; color: var(--yellow);
    letter-spacing: 0.4px;
  }
  .contact-list {
    position: absolute; left: 45px; top: 208px;
    list-style: none;
  }
  .contact-list li {
    display: flex; align-items: center;
    height: 20px; font-size: 15px; color: var(--ink);
  }
  .contact-list svg { width: 14px; height: 14px; margin-right: 7px; fill: var(--green); flex: none; }

  .front__brand {
    position: absolute; left: 350px; top: 195px;
    display: flex; align-items: center; gap: 10px;
  }
  .brand-dot { width: 16px; height: 16px; border-radius: 50%; background: var(--green); }
  .brand-name {
    font-family: "Roboto", Arial, sans-serif;
    font-weight: 700; font-size: 46px; color: var(--green);
  }

  .front__band { position: absolute; bottom: 0; height: 11px; }
  .front__band--yellow { left: 0; width: 202px; background: var(--yellow); }
  .front__band--green  { left: 206px; right: 0; background: var(--green); }

  .back__brand {
    position: absolute; left: 0; right: 0; top: 120px;
    display: flex; justify-content: center; align-items: center; gap: 14px;
  }
  .back__brand .brand-dot { width: 22px; height: 22px; background: var(--yellow); }
  .back__brand .brand-name { font-size: 72px; color: var(--white); }

  .tagline {
    position: absolute; left: 64px; right: 64px; top: 299px;
    display: flex; align-items: center; gap: 4px;
    color: var(--white); font-size: 15px; white-space: nowrap;
  }
  .tagline__rule { flex: 1; height: 1px; }
  .tagline__rule--left  { background: linear-gradient(to right, rgba(255,255,255,0), rgba(255,255,255,0.9)); }
  .tagline__rule--right { background: linear-gradient(to left, rgba(255,255,255,0), rgba(255,255,255,0.9)); }
</style>
</head>
<body>
<main class="canvas">

  <section class="card card--front" aria-label="Business card front">
    <div class="front__accent"></div>
    <h1 class="front__name">TOMAS BILBREA</h1>
    <p class="front__title">MANAGING DIRECTOR</p>

    <ul class="contact-list">
      <li>
        <svg viewBox="0 0 24 24"><path d="M6.6 10.8a15.1 15.1 0 0 0 6.6 6.6l2.2-2.2c.3-.3.7-.4 1-.2 1.1.4 2.3.6 3.6.6.6 0 1 .4 1 1V20c0 .6-.4 1-1 1A17 17 0 0 1 3 4c0-.6.4-1 1-1h3.5c.6 0 1 .4 1 1 0 1.3.2 2.5.6 3.6.1.3 0 .7-.2 1z"/></svg>
        +61 491058264
      </li>
      <li>
        <svg viewBox="0 0 24 24"><path d="M2 5h20v14H2z M4 7v.5l8 5 8-5V7l-8 5z" fill-rule="evenodd"/></svg>
        tomas@kelvarin.com.au
      </li>
      <li>
        <svg viewBox="0 0 24 24"><circle cx="12" cy="12" r="10"/><path d="M12 2c3 3 3 17 0 20M2 12h20" stroke="#f2f2f2" stroke-width="1.6" fill="none"/></svg>
        www.kelvoria.com.au
      </li>
      <li>
        <svg viewBox="0 0 24 24"><path d="M12 1a8 8 0 0 0-8 8c0 6 8 14 8 14s8-8 8-14a8 8 0 0 0-8-8zm0 11a3 3 0 1 1 0-6 3 3 0 0 1 0 6z"/></svg>
        Portvale, Australia
      </li>
    </ul>

    <div class="front__brand">
      <span class="brand-dot"></span>
      <span class="brand-name">Kelvoria</span>
    </div>

    <div class="front__band front__band--yellow"></div>
    <div class="front__band front__band--green"></div>
  </section>

  <section class="card card--back" aria-label="Business card back">
    <div class="back__brand">
      <span class="brand-dot"></span>
      <span class="brand-name">Kelvoria</span>
    </div>
    <p class="tagline">
      <span class="tagline__rule tagline__rule--left"></span>
      Vamos contigo, ya!
      <span class="tagline__rule tagline__rule--right"></span>
    </p>
  </section>

</main>
</body>
</html>
```